Business card for a Exhibition booth fabrication company

Hi. My company would like to change our corporate name card. We are an events and Exhibition stand builder company. We would like our corporate name card to resonate what we do. I need someone to create something unique that relates to the industry that I am in. The graphic designer should be creative to incorporate the elements of my industry and try to blend in well in the design of the card. Our aim is to ensure that we are unique and our card can look different from our competitors.
Updates

Target Market(s)

Marketing and events manager from all companies

Contact Information for Business Card

The business card should have the following details:
Name
Job Title
Email
Website

Colors

Designer to choose colors to be used in the design.

Requirements
Must have
• The card must be look something that is relevant to the service that I am providing. My website is: www.velmora-buildworks.com
• You can see my website to get more information on what service that I am doing
Nice to have
• On the back of my card, I would like to have a globe image with the incorporation of my company logo. This is to indicate that my services can be done in any part of the world.

```html
<!DOCTYPE html>
<html lang="en">
<head>
<meta charset="utf-8">
<title>Velmora Buildworks – Business Card</title>
<link rel="stylesheet" href="https://fonts.googleapis.com/css2?family=Open+Sans:wght@400;600;700&display=swap">
<style>
  :root {
    --page-bg: #e9e6e3;
    --card-white: #ffffff;
    --ink-dark: #4a4a4c;
    --ink-mid: #6d6d70;
    --band-light: #dcdcdd;
    --band-lighter: #ececed;
    --brand-red: #e3161f;
    --text-light: #ffffff;
  }
  * { box-sizing: border-box; margin: 0; padding: 0; }
  html, body { width: 1200px; height: 997px; overflow: hidden; }
  body {
    background: var(--page-bg);
    font-family: "Open Sans", Arial, sans-serif;
    position: relative;
  }
  .card {
    position: absolute;
    width: 520px;
    height: 297px;
    overflow: hidden;
    box-shadow: 0 6px 18px rgba(0,0,0,0.12);
  }
  .card--front { left: 60px; top: 220px; background: var(--card-white); }
  .card--back { left: 620px; top: 480px; background: var(--ink-dark); }

  .card__shapes { position: absolute; inset: 0; }

  .wordmark {
    position: absolute;
    display: flex;
    align-items: center;
    gap: 10px;
    font-weight: 700;
    white-space: nowrap;
  }
  .wordmark__dot {
    width: 18px; height: 18px;
    border-radius: 50%;
    background: var(--brand-red);
    flex: none;
  }
  .card--front .wordmark {
    left: 34px; top: 112px;
    font-size: 15px; letter-spacing: 2px;
    color: var(--ink-mid);
  }
  .card--back .wordmark {
    left: 0; right: 0; top: 132px;
    justify-content: center;
    font-size: 22px; letter-spacing: 3px;
    color: var(--text-light);
  }
  .card--back .wordmark__dot { width: 22px; height: 22px; }

  .contact-list {
    position: absolute;
    right: 20px;
    top: 96px;
    list-style: none;
    font-size: 11px;
    color: var(--ink-mid);
    text-align: right;
  }
  .contact-list li {
    display: flex;
    align-items: center;
    justify-content: flex-end;
    gap: 8px;
    height: 25px;
  }
  .contact-list svg { width: 12px; height: 12px; flex: none; }

  .person {
    position: absolute;
    left: 38px;
    top: 200px;
    color: var(--text-light);
  }
  .person__name { font-size: 17px; font-weight: 700; letter-spacing: 0.5px; }
  .person__title { font-size: 14px; font-weight: 400; margin-top: 2px; }
  .person__phone {
    font-size: 13.5px; margin-top: 4px;
    display: flex; align-items: center; gap: 7px;
  }
  .person__phone svg { width: 12px; height: 12px; }

  .globe-area {
    position: absolute;
    left: 30px; top: 20px; width: 460px; height: 240px;
    border-radius: 40%;
    background: radial-gradient(ellipse at center, rgba(255,255,255,0.09) 0%, rgba(255,255,255,0.03) 60%, rgba(255,255,255,0) 75%);
  }
</style>
</head>
<body>

<section class="card card--front" aria-label="Business card front">
  <svg class="card__shapes" viewBox="0 0 520 297" aria-hidden="true">
    <rect x="310" y="92" width="210" height="2" fill="var(--band-lighter)"/>
    <rect x="310" y="119" width="210" height="2" fill="var(--band-lighter)"/>
    <rect x="310" y="146" width="210" height="3" fill="var(--band-light)"/>
    <polygon points="300,149 520,149 520,297 370,297" fill="var(--band-lighter)"/>
    <polygon points="350,149 430,149 475,210 410,210" fill="var(--band-light)"/>
    <polygon points="0,180 280,180 355,297 0,297" fill="var(--ink-dark)"/>
  </svg>

  <div class="wordmark"><span class="wordmark__dot"></span>VELMORA BUILDWORKS</div>

  <ul class="contact-list">
    <li>info@velmora-buildworks.com
      <svg viewBox="0 0 12 12"><rect x="0.5" y="2" width="11" height="8" fill="var(--brand-red)"/><path d="M0.5 2 L6 6.5 L11.5 2" stroke="#fff" fill="none" stroke-width="1"/></svg>
    </li>
    <li>www.velmora-buildworks.com
      <svg viewBox="0 0 12 12"><circle cx="6" cy="6" r="5.3" fill="none" stroke="var(--brand-red)" stroke-width="1.2"/><ellipse cx="6" cy="6" rx="2.3" ry="5.3" fill="none" stroke="var(--brand-red)" stroke-width="1"/><line x1="0.7" y1="6" x2="11.3" y2="6" stroke="var(--brand-red)" stroke-width="1"/></svg>
    </li>
  </ul>

  <div class="person">
    <p class="person__name">DANIEL ARCOTT</p>
    <p class="person__title">President</p>
    <p class="person__phone">
      <svg viewBox="0 0 12 12"><path d="M3 0.8 L4.6 3.4 L3.6 4.6 C4.3 6.2 5.8 7.7 7.4 8.4 L8.6 7.4 L11.2 9 L10 11.2 C5 11 1 7 0.8 2 Z" fill="var(--text-light)"/></svg>
      +974 55501842
    </p>
  </div>
</section>

<section class="card card--back" aria-label="Business card back">
  <div class="globe-area" role="img" aria-label="Faint dotted world map spanning the card"></div>
  <div class="wordmark"><span class="wordmark__dot"></span>VELMORA BUILDWORKS</div>
</section>

</body>
</html>
```